New menu rebranding for Asian fusion

I have my current menu attached, but I want to change it and make it more attractive. The restaurant is an Asian Fusion. Food from Thailand, China, Japan, Indonesia, Malaysia, Cambodia. We cater to mid to high end consumers with an educated and sophisticated pallet. Maybe try a modern twist, or an authentic variation, maybe a mix. Please don't play with the logo too much, but feel free to play with the pattern. I also want to have as many pictures of dishes visible as possible. Additionally, keep in mind that the menu will be in two languages, so please design accordingly. Feel free to play around with the format of the menu and the logo too if you get carried away. Keep it in mind that this is also a take out menu too. Please check out the Instagram account lotus_crate As well as facebook etc. Let me know if you need any additional files. Thx and appreciated.
Updates

I have made an update to the Menu. It's not the original file. It's smaller now. Please see the attached PDF file. Best regards, Added Monday, February 02, 2015

Target Market(s)

Mid to high end

Industry/Entity Type

Restaurant

Number of Pages Required

3 page

Requirements
Must have
• dual language friendly. At least make space for it.
• Must keep logo.
Nice to have
• Would be nice to stick to same theme, not too much change to branding.

```html
<!DOCTYPE html>
<html lang="en">
<head>
<meta charset="utf-8">
<title>Lotus Crate Menu</title>
<link href="https://fonts.googleapis.com/css2?family=Michroma&family=Questrial&display=swap" rel="stylesheet">
<style>
:root{
  --bg:#e1e1e1;
  --paper:#ffffff;
  --ink:#111111;
  --orange:#f39322;
  --green:#2ea836;
  --rule:#555555;
  --pattern:#2e2e2e;
}
*{margin:0;padding:0;box-sizing:border-box}
html,body{width:1200px;height:1000px;overflow:hidden;background:var(--bg)}
body{position:relative;font-family:"Michroma",sans-serif;color:var(--ink)}
.spread{position:absolute;background:var(--paper);border:1px solid var(--rule)}
.cover{left:15px;top:9px;width:948px;height:476px}
.fold{position:absolute;top:0;bottom:0;left:473px;width:1px;background:var(--rule)}
.pattern-band{position:absolute;background:var(--pattern)}
.cover .pattern-band{left:0;right:0;top:343px;bottom:0}
.brand{position:absolute;top:158px;font-family:"Questrial",sans-serif}
.brand.left{left:30px}
.brand.right{right:32px;text-align:right}
.brand .web{color:var(--orange);font-size:14px;letter-spacing:.5px}
.brand .name{font-family:"Michroma",sans-serif;font-size:27px;line-height:32px;color:var(--ink);letter-spacing:1px;text-transform:lowercase}
.brand .tagline{font-size:18px;color:#222;margin-top:1px;letter-spacing:.3px}
.brand .contacts{display:flex;gap:18px;margin-top:6px;font-size:12px;color:var(--orange);align-items:center}
.brand.right .contacts{justify-content:flex-end}
.contact{display:flex;align-items:center;gap:7px}
.contact svg{width:13px;height:13px}

.inside{left:231px;top:509px;width:949px;height:476px}
.inside .pattern-band.top{left:0;top:12px;width:473px;height:24px}
.inside .pattern-band.bottom{left:0;top:438px;width:473px;height:24px}
.section-bar{position:absolute;top:51px;height:25px;background:var(--ink);color:#fff;display:flex;align-items:center}
.section-bar .no{font-size:7px;margin-left:18px}
.section-bar .title{font-size:12px;flex:1;text-align:center}
.bar-appetizers{left:0;width:212px}
.bar-appetizers .title{padding-right:24px}
.bar-arabic{left:259px;width:214px}
.bar-arabic .title{padding-right:36px}
.menu-list{position:absolute;left:16px;top:104px;width:230px;list-style:none}
.dish{position:relative;height:64.5px;padding-left:28px}
.dish .code{position:absolute;left:0;top:2px;font-size:9px}
.dish .name{font-size:11px}
.dish .desc{font-size:8px;line-height:10.5px;color:var(--orange);width:170px}
.dish .price{position:absolute;left:213px;top:2px;font-size:9px}

.photo{position:absolute;left:473px;top:0;width:475px;height:474px;
  background:radial-gradient(ellipse at 60% 65%,#d8b75a 0%,#c7a14a 35%,#e9e2cf 70%,#f4f4f4 100%)}
.caption{position:absolute;background:var(--ink);text-align:center;line-height:1.2}
.caption .dish-name{color:#fff}
.caption .lang{color:var(--orange)}
.caption.feature{left:807px;top:53px;width:141px;height:40px;padding-top:4px;font-size:11px}
.thumb{position:absolute;top:311px;width:124px;border:2px solid var(--orange);border-bottom:0;height:123px}
.thumb.dendeng{left:492px;background:linear-gradient(160deg,#8e2a2a,#4a1212)}
.thumb.calamari{left:624px;background:linear-gradient(160deg,#d9dde0,#d89b3c 60%,#b8772a)}
.caption.small{top:433px;width:124px;height:21px;font-size:7px;padding-top:2px}
.caption.small.c1{left:492px}
.caption.small.c2{left:624px}
</style>
</head>
<body>

<section class="spread cover">
  <div class="fold"></div>

  <div class="brand left">
    <div class="web">www.lotuscrate.co</div>
    <div class="name">lotus crate</div>
    <div class="tagline">think inside the box</div>
    <div class="contacts">
      <span class="contact"><svg viewBox="0 0 14 14"><circle cx="7" cy="7" r="7" fill="#f39322"/><path d="M4.3 3.6l1.4-.3.8 1.9-.9.7a5 5 0 0 0 2.5 2.5l.7-.9 1.9.8-.3 1.4c-3.4.2-6.3-2.7-6.1-6.1z" fill="#fff"/></svg>012 5804411</span>
      <span class="contact"><svg viewBox="0 0 14 14"><circle cx="7" cy="7" r="7" fill="#2ea836"/><path d="M4.3 3.6l1.4-.3.8 1.9-.9.7a5 5 0 0 0 2.5 2.5l.7-.9 1.9.8-.3 1.4c-3.4.2-6.3-2.7-6.1-6.1z" fill="#fff"/></svg>0536218840</span>
    </div>
  </div>

  <div class="brand right">
    <div class="web">www.lotuscrate.co</div>
    <div class="name">lotus crate</div>
    <div class="tagline">think inside the box</div>
    <div class="contacts">
      <span class="contact"><svg viewBox="0 0 14 14"><circle cx="7" cy="7" r="7" fill="#f39322"/><path d="M4.3 3.6l1.4-.3.8 1.9-.9.7a5 5 0 0 0 2.5 2.5l.7-.9 1.9.8-.3 1.4c-3.4.2-6.3-2.7-6.1-6.1z" fill="#fff"/></svg>012 5804411</span>
      <span class="contact"><svg viewBox="0 0 14 14"><circle cx="7" cy="7" r="7" fill="#2ea836"/><path d="M4.3 3.6l1.4-.3.8 1.9-.9.7a5 5 0 0 0 2.5 2.5l.7-.9 1.9.8-.3 1.4c-3.4.2-6.3-2.7-6.1-6.1z" fill="#fff"/></svg>0536218840</span>
    </div>
  </div>

  <div class="pattern-band" role="img" aria-label="Repeating black and white brand pattern band"></div>
</section>

<section class="spread inside">
  <div class="pattern-band top" role="img" aria-label="Repeating brand pattern strip"></div>

  <div class="section-bar bar-appetizers"><span class="no">No.</span><span class="title">Appetizers</span></div>
  <div class="section-bar bar-arabic"><span class="no">No.</span><span class="title">Arrabic</span></div>

  <ul class="menu-list">
    <li class="dish"><span class="code">101</span><div class="name">Chicken Satay</div><div class="desc">Bar BQ chicken skewers marinated in thai herbs served with sweet tangy peanut sauce</div><span class="price">25</span></li>
    <li class="dish"><span class="code">102</span><div class="name">Shrimp Satay</div><div class="desc">Bar BQ shrimp skewers marinated in thai herbs served with sweet tangy peanut sauce</div><span class="price">30</span></li>
    <li class="dish"><span class="code">103</span><div class="name">Dendeng</div><div class="desc">Our signature appetizer, crispy beef tossed in an aromatic spicy sauce with fried onions</div><span class="price">38</span></li>
    <li class="dish"><span class="code">104</span><div class="name">Calamari</div><div class="desc">Tender calamari lightly dusted and wok fried served with a chili soy dipping sauce</div><span class="price">28</span></li>
    <li class="dish"><span class="code">105</span><div class="name">Spring Rolls</div><div class="desc">Crispy fried spring rolls filled with fresh vegetables served with a sweet chilli dipping sauce</div><span class="price">23</span></li>
  </ul>

  <div class="pattern-band bottom" role="img" aria-label="Repeating brand pattern strip"></div>

  <div class="photo" role="img" aria-label="Photo of grilled chicken satay skewers with peanut sauce and cucumber salad"></div>
  <div class="caption feature"><div class="dish-name">Chicken Satay</div><div class="lang">Arabic</div></div>

  <div class="thumb dendeng" role="img" aria-label="Photo of dendeng crispy beef with red chili"></div>
  <div class="caption small c1"><div class="dish-name">Dendeng</div><div class="lang">Arabic</div></div>

  <div class="thumb calamari" role="img" aria-label="Photo of fried calamari rings with lime"></div>
  <div class="caption small c2"><div class="dish-name">Calamari</div><div class="lang">Arabic</div></div>
</section>

</body>
</html>
```